Breakfast Cafe - The Sunny Nook

It is for my breakfast and lunch cafe with a hawaiian / beach theme. I am open 7 days a week from 7am to 2pm. We serve traditional American food such as omelettes, pancakes, burgers and sandwiches. I'll upload my old card and my new logo to be used. We have a lot of day to day regulars who eat there during the week, our t-shirts actually say 'Locals Only' on them. Hope this helps. Thanks.

Target Market(s)

anyone who has an appetite!

Industry/Entity Type

American Restaurant

Contact Information for Business Card

4815C Marlow Grove Avenue
Long Beach, California
(555) 731-2294

Requirements
Must have
• Address and phone number easily readable.
Nice to have
• beach or tropical theme

```html
<!DOCTYPE html>
<html lang="en">
<head>
<meta charset="utf-8">
<title>The Sunny Nook – Business Cards</title>
<link rel="stylesheet" href="https://fonts.googleapis.com/css2?family=Lato:wght@400;700;900&display=swap">
<style>
  :root {
    --backdrop: #1fae9a;
    --sky-top: #2c5d95;
    --sky-mid: #5b87b5;
    --sea: #2a7fa6;
    --sand: #c9b58e;
    --white: #ffffff;
    --rust: #b26212;
    --rust-light: #d88a32;
    --ink: #1c1208;
  }
  * { margin: 0; padding: 0; box-sizing: border-box; }
  html, body { width: 1200px; height: 802px; overflow: hidden; }
  body {
    background: var(--backdrop);
    font-family: "Lato", Arial, sans-serif;
    position: relative;
  }
  .card {
    position: absolute;
    top: 274px;
    width: 445px;
    height: 266px;
    overflow: hidden;
  }
  .card--front { left: 134px; }
  .card--back { left: 624px; background: var(--rust); }

  .beach-photo {
    position: absolute; inset: 0;
    background: linear-gradient(180deg, var(--sky-top) 0%, var(--sky-mid) 62%, var(--sea) 80%, var(--sea) 88%, var(--sand) 100%);
  }
  .front-content {
    position: absolute; left: 22px; top: 26px; right: 20px;
    color: var(--white);
  }
  .brand-name {
    font-weight: 900; font-size: 38px; line-height: 1; letter-spacing: 0.5px;
  }
  .tagline { font-size: 21px; margin-top: 19px; }
  .phone {
    display: flex; align-items: center; gap: 7px;
    font-size: 17px; margin-top: 15px;
  }
  .phone svg { width: 17px; height: 17px; }
  .address { font-size: 16px; line-height: 20px; margin-top: 14px; }
  .hours { font-size: 20px; font-weight: 700; margin-top: 12px; }

  .emblem {
    position: absolute; left: 153px; top: 31px;
    width: 138px; height: 138px; border-radius: 50%;
    background: var(--rust-light);
  }
  .back-name {
    position: absolute; left: 0; right: 0; top: 160px;
    text-align: center; color: var(--white);
    font-weight: 900; font-size: 34px; line-height: 1;
  }
  .back-location {
    position: absolute; left: 0; right: 0; top: 205px;
    text-align: center; color: var(--white);
    font-weight: 700; font-size: 10px; letter-spacing: 3px;
  }
  .menu-line {
    position: absolute; left: 0; right: 0; top: 228px;
    text-align: center; color: var(--ink); font-size: 15px;
  }
</style>
</head>
<body>
  <section class="card card--front">
    <div class="beach-photo" role="img" aria-label="Photo of a sunny tropical beach with palm trees, blue sky and ocean"></div>
    <div class="front-content">
      <h1 class="brand-name">The Sunny Nook</h1>
      <p class="tagline">Family owned and operated!</p>
      <p class="phone">
        <svg viewBox="0 0 20 20" aria-hidden="true">
          <rect width="20" height="20" rx="3" fill="#fff"/>
          <path d="M6.2 4.5l2 2.6-1.2 1.4c.8 1.7 2 2.9 3.7 3.7l1.4-1.2 2.6 2-1.2 2c-4.6-.3-8.2-3.9-8.5-8.5z" fill="#2c5d95"/>
        </svg>
        (555) 731-2294
      </p>
      <p class="address">4815C Marlow Grove Avenue<br>Long Beach, California</p>
      <p class="hours">Breakfast &amp; Lunch 7am - 2pm Daily</p>
    </div>
  </section>

  <section class="card card--back">
    <div class="emblem"></div>
    <h2 class="back-name">The Sunny Nook</h2>
    <p class="back-location">LONG BEACH, CA</p>
    <p class="menu-line">Omelettes | Pancakes | Burgers | Sandwiches</p>
  </section>
</body>
</html>
```